Naturopath Practitioner Card Design

I am a naturopath needing a design for a business card mainly to show that I am a naturopath and have some contact details to give to prospective clients. I am open minded about the design and what is on the second side of the card whether it just be some artwork or space for details, appointment times etc. Naturopathy is the practice of natural medicine that uses a holistic approach and incorporates herbal and nutritional medicine.

Industry/Entity Type

Business

Contact Information for Business Card

Tom Rudd NaturopathBHSc (Naturopathy) Member WHPG 0487 925 316 tom.rudd@mailexample.com www.tomruddnaturopathy.example.au

Requirements
Nice to have
• Would prefer some kind of original pattern/art work/logo rather than an image, not fussed if its very simple/basic
• I am open to any colour but think I would prefer a more earthy sandy clay etc type style than the greens that are commonly associated with naturopathy.
Should not have
• Don't really want to have generic stock images on it

```html
<!DOCTYPE html>
<html lang="en">
<head>
<meta charset="utf-8">
<title>Tom Rudd Naturopath – Business Card</title>
<link rel="stylesheet" href="https://fonts.googleapis.com/css2?family=Didact+Gothic&display=swap">
<style>
  :root {
    --leaf: #86a33d;
    --leaf-dark: #6f8b2c;
    --paper: #ffffff;
    --backdrop: #1e1e1e;
    --card-w: 640px;
    --card-h: 370px;
    --radius: 22px;
  }
  * { box-sizing: border-box; margin: 0; padding: 0; }
  html, body {
    width: 1200px; height: 912px; overflow: hidden;
    background: var(--backdrop);
    font-family: "Didact Gothic", "Century Gothic", sans-serif;
  }
  .sheet {
    width: 1200px; height: 912px;
    display: flex; flex-direction: column; align-items: center; justify-content: center;
    gap: 32px;
  }
  .card {
    width: var(--card-w); height: var(--card-h);
    border-radius: var(--radius);
    overflow: hidden;
    position: relative;
  }

  /* Appointment side */
  .appointment-card { background: var(--paper); color: var(--leaf); display: flex; flex-direction: column; }
  .appointment-body { flex: 1; padding: 26px 36px 0; }
  .appointment-title {
    text-align: center; font-size: 26px; letter-spacing: 0.5px;
    margin: 0 0 4px 120px;
  }
  .form-row { display: flex; align-items: flex-end; height: 34px; font-size: 16px; gap: 6px; }
  .form-row .label { white-space: nowrap; }
  .form-row .blank { flex: 1; border-bottom: 1.5px solid var(--leaf); height: 1px; margin-bottom: 5px; }
  .form-row .blank.date { flex: 1.05; }
  .form-row .ampm { white-space: nowrap; font-size: 16px; }
  .day-row {
    display: flex; justify-content: space-between; align-items: center;
    margin-top: 14px; font-size: 20px; text-transform: uppercase;
  }
  .day { display: flex; align-items: center; gap: 4px; }
  .tick-box { width: 20px; height: 20px; border: 2.5px solid var(--leaf); }
  .notice-band {
    height: 88px; background: var(--leaf); color: var(--paper);
    display: flex; flex-direction: column; justify-content: center; align-items: center;
    font-size: 16px; text-transform: uppercase; letter-spacing: 0.3px; text-align: center; line-height: 1.4;
  }

  /* Front side */
  .front-card { background: var(--leaf); color: var(--paper); }
  .practitioner { position: absolute; left: 38px; top: 34px; }
  .practitioner-name { font-size: 31px; letter-spacing: 0.6px; }
  .practitioner-credential { font-size: 16px; margin-top: 2px; }
  .contact-list {
    position: absolute; right: 40px; bottom: 42px;
    list-style: none; text-align: right; font-size: 20px; letter-spacing: 0.4px; line-height: 1.35;
  }
  .contact-list li { display: flex; align-items: center; justify-content: flex-end; gap: 12px; }
  .contact-list svg { width: 20px; height: 20px; flex: none; }
  .base-rule {
    position: absolute; left: 0; right: 0; bottom: 22px;
    height: 3px; background: var(--paper);
  }
</style>
</head>
<body>
<main class="sheet">

  <section class="card appointment-card" aria-label="Appointment card">
    <div class="appointment-body">
      <h2 class="appointment-title">Appointment</h2>
      <div class="form-row"><span class="label">Name:</span><span class="blank"></span></div>
      <div class="form-row"><span class="label">Date:</span><span class="blank date"></span><span class="label">Time :</span><span class="blank"></span><span class="ampm">am / pm</span></div>
      <div class="form-row"><span class="label">Date:</span><span class="blank date"></span><span class="label">Time :</span><span class="blank"></span><span class="ampm">am / pm</span></div>
      <div class="form-row"><span class="label">Date:</span><span class="blank date"></span><span class="label">Time :</span><span class="blank"></span><span class="ampm">am / pm</span></div>
      <div class="form-row"><span class="label">Date:</span><span class="blank date"></span><span class="label">Time :</span><span class="blank"></span><span class="ampm">am / pm</span></div>
      <div class="day-row">
        <span class="day">Mon<span class="tick-box"></span></span>
        <span class="day">Tue<span class="tick-box"></span></span>
        <span class="day">Wed<span class="tick-box"></span></span>
        <span class="day">Thu<span class="tick-box"></span></span>
        <span class="day">Fri<span class="tick-box"></span></span>
        <span class="day">Sat<span class="tick-box"></span></span>
      </div>
    </div>
    <div class="notice-band">
      <p>Please notify us 24hrs in advance if you need to cancel</p>
      <p>your appointment</p>
    </div>
  </section>

  <section class="card front-card" aria-label="Business card front">
    <div class="practitioner">
      <h1 class="practitioner-name">Tom Rudd Naturopath</h1>
      <p class="practitioner-credential">BHSc (Naturopathy)</p>
    </div>
    <ul class="contact-list">
      <li>tom.rudd@mailexample.com
        <svg viewBox="0 0 20 20" aria-hidden="true"><rect x="1.5" y="4.5" width="17" height="11" fill="none" stroke="#fff" stroke-width="1.6"/><path d="M1.5 4.5 10 11 18.5 4.5" fill="none" stroke="#fff" stroke-width="1.6"/></svg>
      </li>
      <li>www.tomruddnaturopathy.example.au
        <svg viewBox="0 0 20 20" aria-hidden="true"><g fill="none" stroke="#fff" stroke-width="1.4"><circle cx="10" cy="10" r="8"/><ellipse cx="10" cy="10" rx="3.6" ry="8"/><path d="M2 10h16M3.2 6h13.6M3.2 14h13.6"/></g></svg>
      </li>
    </ul>
    <div class="base-rule"></div>
  </section>

</main>
</body>
</html>
```